BOLD & MINIMALIST DESIGN NEEDED

We want a very bold but minimalistic business card design that is impactful and utilizes both sides of the business card. Our current logo is included for your use.

We want bold fonts and good use of negative space. We don't want the logo to overpower the design.

Target Market(s)

Professionals who are building new commercial buildings.

Industry/Entity Type

Construction

Contact Information for Business Card

Name, Title, email, office phone, cell phone, website

Font styles to use
Serif
Sans Serif

Requirements
Must have
• Bold design!

```html
<!DOCTYPE html>
<html lang="en">
<head>
<meta charset="utf-8">
<title>Ridgeline Design + Build — Business Card</title>
<link rel="stylesheet" href="https://fonts.googleapis.com/css2?family=Montserrat:wght@400;500;800&display=swap">
<style>
  :root {
    --green: #86c443;
    --green-light: #cfe8b0;
    --ink: #111111;
    --paper: #ffffff;
    --backdrop: #2b2b2b;
    --card-w: 540px;
    --card-h: 310px;
  }
  * { box-sizing: border-box; margin: 0; padding: 0; }
  html, body { width: 1200px; height: 960px; overflow: hidden; }
  body {
    background: var(--backdrop);
    font-family: "Montserrat", sans-serif;
    position: relative;
  }
  .card {
    position: absolute;
    width: var(--card-w);
    height: var(--card-h);
    border-radius: 18px;
    overflow: hidden;
    box-shadow: 0 14px 30px rgba(0,0,0,.45);
  }
  /* Front side */
  .card-front {
    left: 90px; top: 110px;
    background: var(--green);
    display: flex; align-items: center; justify-content: center;
  }
  .wordmark {
    color: var(--paper);
    font-weight: 800;
    text-align: center;
    line-height: 1.05;
    display: flex; align-items: center; gap: 16px;
  }
  .wordmark-mark { width: 26px; height: 26px; background: currentColor; }
  .wordmark-name { font-size: 50px; letter-spacing: 1px; }
  .wordmark-tag { font-size: 17px; letter-spacing: 7px; border-top: 2px solid currentColor; padding-top: 6px; margin-top: 6px; }

  /* Back side */
  .card-back {
    left: 570px; top: 530px;
    background: var(--paper);
  }
  .back-wordmark {
    position: absolute; left: 34px; top: 88px;
    color: var(--ink);
  }
  .back-wordmark .wordmark-mark { width: 18px; height: 18px; }
  .back-wordmark .wordmark-name { font-size: 30px; }
  .back-wordmark .wordmark-tag { font-size: 11px; letter-spacing: 4px; padding-top: 4px; margin-top: 4px; }
  .wordmark-text { display: flex; flex-direction: column; }
  .divider {
    position: absolute; left: 290px; top: 52px;
    width: 2px; height: 150px; background: var(--green);
  }
  .contact { position: absolute; left: 310px; top: 46px; }
  .contact-name { color: var(--green); font-weight: 800; font-size: 22px; letter-spacing: .5px; }
  .contact-title { color: var(--ink); font-size: 13px; font-weight: 500; margin: 2px 0 10px; }
  .contact-list { list-style: none; }
  .contact-list li {
    display: flex; align-items: center; gap: 9px;
    font-size: 13px; color: var(--ink); margin-bottom: 7px;
  }
  .contact-list svg { width: 14px; height: 14px; fill: var(--green); flex: none; }
  .address-band {
    position: absolute; left: 0; right: 0; bottom: 34px; height: 36px;
    background: linear-gradient(90deg, var(--green-light) 0%, var(--green) 45%, var(--green) 100%);
    display: flex; align-items: center; justify-content: flex-end; padding-right: 32px;
    font-size: 13px; font-weight: 500; color: var(--ink);
  }
</style>
</head>
<body>
  <section class="card card-front" aria-label="Card front">
    <div class="wordmark">
      <span class="wordmark-mark"></span>
      <div class="wordmark-text">
        <span class="wordmark-name">RIDGELINE</span>
        <span class="wordmark-tag">DESIGN + BUILD</span>
      </div>
    </div>
  </section>

  <section class="card card-back" aria-label="Card back">
    <div class="wordmark back-wordmark">
      <span class="wordmark-mark"></span>
      <div class="wordmark-text">
        <span class="wordmark-name">RIDGELINE</span>
        <span class="wordmark-tag">DESIGN + BUILD</span>
      </div>
    </div>
    <div class="divider"></div>
    <div class="contact">
      <p class="contact-name">MARCUS HALDEN</p>
      <p class="contact-title">Managing Director</p>
      <ul class="contact-list">
        <li><svg viewBox="0 0 24 24"><path d="M6.6 10.8a15 15 0 0 0 6.6 6.6l2.2-2.2c.3-.3.7-.4 1-.2 1.1.4 2.3.6 3.6.6.6 0 1 .4 1 1V20c0 .6-.4 1-1 1A17 17 0 0 1 3 4c0-.6.4-1 1-1h3.5c.6 0 1 .4 1 1 0 1.3.2 2.5.6 3.6.1.3 0 .7-.2 1z"/></svg>555-214-0387</li>
        <li><svg viewBox="0 0 24 24"><path d="M3 9c0-3 4-5 9-5s9 2 9 5v2h-5V9H8v2H3zM6 12h12l2 8H4z"/></svg>000 000 0000</li>
        <li><svg viewBox="0 0 24 24"><path d="M2 5h20v14H2zM3 6l9 7 9-7v2l-9 7-9-7z"/></svg>info@yourmail.com</li>
        <li><svg viewBox="0 0 24 24"><circle cx="12" cy="12" r="10"/></svg>www.yourwebsite.com</li>
      </ul>
    </div>
    <div class="address-band">482 Cedar Crest Ave, Ste 100, Dallas, TX 75201</div>
  </section>
</body>
</html>
```